Web Page Design for Major Airline Consolidator

We need a new design for an airline consolidator based out of NY. We'd really like to get the design as quickly as possible.

Here is a *very* rough mockup of what the site could look like, along with 3 main competitor's sites. Needless to say, they want a design that looks much better than their competitors. Please note that the mockup is an idea only, feel free to enhance / improve upon it.

Mockup - https://plankrafe.com/tvorel/KQPMzaLu

Competitors:
- http://www.brellintour.com/
- http://www.skorvatix.com/home2.html
- https://www.dulmerok.com/index.php

Target Market(s)

target markets are identified in the mockup

Industry/Entity Type

Airline

Number of Pages Required

1 page

Requirements
Must have
• need space on the left side for a travel request form which is missing in the mockup. Form should have standard air booking fields (to, from, date arrival & departure, travel class, etc).

```html
<!DOCTYPE html>
<html lang="en">
<head>
<meta charset="utf-8">
<title>Kestral Tours – Airline Consolidator</title>
<link rel="stylesheet" href="https://fonts.googleapis.com/css2?family=Open+Sans:ital,wght@0,400;0,600;0,700;1,400;1,600&display=swap">
<style>
:root{
  --red:#e04848;
  --red-dark:#c93838;
  --blue:#2f7fc1;
  --ink:#333;
  --muted:#777;
  --line:#dcdcdc;
  --band:#eeeeee;
  --white:#fff;
  --sky-top:#3d6fa8;
  --sky-bottom:#a9c8e6;
}
*{box-sizing:border-box;margin:0;padding:0}
html,body{width:1200px;height:3945px;overflow:hidden}
body{font-family:"Open Sans",Arial,sans-serif;color:var(--ink);background:var(--white);position:relative;font-size:14px}
.abs{position:absolute}
.btn{display:inline-block;background:var(--red);color:var(--white);font-weight:600;text-transform:uppercase;text-align:center;border-radius:3px;font-size:15px;padding:11px 0}
h2.section-title{font-size:20px;font-weight:600;letter-spacing:.5px;text-align:center;text-transform:uppercase;color:#222}

/* header */
.site-header{top:0;left:0;width:1200px;height:100px}
.logo{left:100px;top:22px;display:flex;align-items:center;gap:12px}
.logo-mark{width:46px;height:46px;border-radius:50%;background:#555}
.logo-name{font-size:27px;font-weight:600;color:#444;line-height:1}
.logo-tag{font-size:11px;color:#666;margin-top:4px}
.social{right:100px;top:16px;display:flex;gap:10px}
.social span{width:14px;height:14px;border-radius:50%;background:#9a9a9a}
.account-links{right:100px;top:64px;font-size:13px;color:#777;display:flex;gap:26px}

/* nav */
.main-nav{top:100px;left:100px;width:1000px;height:26px;border-top:1px solid var(--line);display:flex;justify-content:space-between;align-items:center;font-size:12px;text-transform:uppercase;color:#555}
.main-nav .active{color:var(--red);font-weight:600}

/* hero */
.hero{top:126px;left:0;width:1200px;height:566px;background:linear-gradient(180deg,var(--sky-top) 0%,#6b9bcd 45%,var(--sky-bottom) 100%)}
.hero-plane{left:0;top:0;width:1200px;height:566px;background:radial-gradient(ellipse 520px 180px at 560px 260px,rgba(235,240,246,.85),rgba(235,240,246,0) 70%)}
.slide-arrow{top:200px;width:52px;height:56px;background:var(--red);display:flex;align-items:center;justify-content:center}
.promo{left:110px;top:84px;width:640px;height:120px;background:rgba(40,70,110,.55)}
.promo h1{color:var(--white);font-size:30px;font-weight:600;text-align:center;margin-top:14px;letter-spacing:.5px}
.promo .stars{color:var(--white);text-align:center;font-size:16px;letter-spacing:4px;margin-top:4px}
.promo .reviews{color:var(--white);text-align:center;font-size:14px;text-decoration:underline}
.signup{left:756px;top:84px;width:362px;height:196px;background:var(--red);padding:14px 34px}
.signup .field{height:36px;background:#f08a8a;color:var(--white);font-size:14px;text-align:center;line-height:36px;margin-bottom:12px;border-radius:2px}
.signup .cta{width:190px;margin:14px auto 0;background:#333;color:var(--white);text-align:center;font-size:15px;padding:10px 0}

.flight-search{left:115px;top:302px;width:985px;height:262px;background:rgba(210,225,240,.92)}
.fs-title{height:30px;line-height:30px;text-align:center;font-weight:700;font-size:17px;color:#2b4a70;border-bottom:1px solid rgba(255,255,255,.7)}
.fs-body{position:relative;height:232px}
.inp{position:absolute;height:32px;background:var(--white);border:1px solid #c7d3e0;font-size:12.5px;color:#666;line-height:30px;padding-left:8px}
.inp.dark{background:#5f7f9f;color:var(--white);border-color:#5f7f9f}
.radio{position:absolute;font-size:13px;color:#333;display:flex;align-items:center;gap:6px}
.radio i{width:11px;height:11px;border-radius:50%;background:var(--white);border:1px solid #999;display:inline-block}
.radio i.on{background:#333}
.fs-link{position:absolute;font-size:13px;color:#333}
.search-btn{position:absolute;left:840px;top:176px;width:120px;height:38px;background:var(--red);color:var(--white);font-weight:700;text-align:center;line-height:38px;font-size:16px}

/* agents */
.agents{top:707px;left:0;width:1200px;height:420px}
.agents h2{margin-top:20px}
.agent-col{top:74px;width:290px;text-align:center}
.agent-icon{width:66px;height:66px;margin:0 auto}
.agent-col h3{color:var(--blue);font-size:16px;font-weight:600;text-transform:uppercase;margin-top:10px}
.agent-col .sub{font-size:13px;color:#555;margin-top:2px}
.agent-col ul{list-style:none;font-size:13px;color:#555;margin-top:12px;line-height:1.6}
.agent-col .more{font-size:13px;color:#555;margin-top:6px}
.agent-col .btn{width:186px;margin-top:14px}

/* welcome */
.welcome{top:1133px;left:0;width:1200px;height:262px;background:var(--band);text-align:center}
.welcome h2{margin-top:40px}
.welcome p{width:1000px;margin:18px auto 0;font-size:14px;line-height:1.9;color:#444}
.welcome .btn{width:116px;font-size:12px;padding:7px 0;margin-top:20px}

/* ceo */
.ceo{top:1398px;left:0;width:1200px;height:405px;background:linear-gradient(180deg,#e9ebed,#f4f5f6)}
.ceo-photo{left:90px;top:0;width:310px;height:405px;background:linear-gradient(180deg,#d9d4cf 0%,#5d6770 55%,#3d444c 100%)}
.ceo blockquote{left:470px;top:110px;width:600px;text-align:center;font-style:italic;font-weight:600;font-size:29px;line-height:1.3;color:#222}
.ceo .sig{left:470px;top:300px;width:600px;text-align:center;font-size:14px;color:#444}
.ceo .sig hr{width:40px;margin:10px auto 0;border:0;border-top:2px solid var(--red)}

/* divisions & employees */
.divisions{top:1803px;left:0;width:1200px;height:300px}
.divisions .col-left{left:0;top:0;width:570px;height:300px;background:#f3f3f3;text-align:center}
.divisions h3{font-size:19px;font-weight:600;text-transform:uppercase;margin-top:22px;color:#222;text-align:center}
.divisions .col-left p{width:300px;margin:20px auto 0;font-size:13px;line-height:1.5;color:#555}
.divisions .col-left ul{list-style:none;margin-top:14px;font-size:13px;color:var(--blue);text-decoration:underline;line-height:1.6}
.divisions .col-left .more{margin-top:16px;font-size:14px;color:#444}
.employees{left:600px;top:0;width:600px;height:300px}
.emp{top:90px;width:120px;text-align:center;font-size:12px;color:#444}
.emp .photo{width:120px;height:130px;background:linear-gradient(180deg,#f2f2f2,#c9ccd0)}
.emp b{display:block;font-weight:600;margin-top:6px}
.emp-arrow{top:136px;font-size:30px;color:#bbb}

/* business */
.business{top:2155px;left:0;width:1200px;height:320px}
.business h2{font-size:20px}
.business .tag{color:var(--red);text-align:center;font-size:16px;margin-top:4px;text-transform:uppercase}
.biz-list{left:140px;top:76px;list-style:none}
.biz-list li{display:flex;align-items:center;gap:12px;font-size:16px;margin-bottom:13px;color:#222}
.biz-list li span{width:30px;height:30px;border-radius:50%;background:var(--red);color:var(--white);font-weight:700;text-align:center;line-height:30px;font-size:15px}
.business .btn{left:400px;top:268px;width:320px;font-size:15px;padding:10px 0}
.agent-photo{left:880px;top:0;width:240px;height:300px;background:radial-gradient(circle at 50% 45%,#f1dcc9 0%,#e8cdb4 35%,rgba(255,255,255,0) 70%)}

/* places */
.places{top:2517px;left:0;width:1200px;height:476px}
.place{top:70px;width:226px;text-align:center}
.place .photo{height:202px}
.place h4{font-size:16px;font-weight:600;margin-top:14px}
.place p{font-size:13px;color:#555;line-height:1.4;margin-top:4px}
.place .price{color:var(--blue);font-size:17px;font-weight:600;margin-top:10px}
.place .btn{width:190px;margin-top:14px}
.round-arrow{top:160px;width:34px;height:34px;border-radius:50%;background:var(--red);display:flex;align-items:center;justify-content:center}
.see-all{right:90px;top:448px;font-size:12px;color:#555}

/* group */
.group{top:3020px;left:0;width:1200px;height:550px}
.group .photo{top:60px;width:430px;height:298px}
.group-card{top:60px;width:430px;text-align:center}
.group-card h4{margin-top:316px;font-size:16px;font-weight:600;text-transform:uppercase}
.group-card p{font-size:13px;color:#555;line-height:1.5;margin-top:8px}
.group-card .btn{width:190px;margin-top:16px}

/* trusted */
.trusted{top:3580px;left:0;width:1200px;height:190px;border-top:1px solid var(--line)}
.trusted h2{margin-top:24px}
.badge{top:86px;width:110px;height:72px;background:#c9ccd2;border-radius:4px}

/* footer */
.site-footer{top:3783px;left:0;width:1200px;height:162px;background:#f5f5f5;border-top:1px solid var(--line)}
.footer-logo{left:100px;top:28px;display:flex;align-items:center;gap:12px}
.footer-logo .logo-mark{background:#777}
.contact{left:600px;top:30px;font-size:11px;color:#777;line-height:2}
.contact div{display:flex;align-items:center;gap:8px}
.footer-social{right:90px;top:48px;display:flex;gap:12px}
.footer-social span{width:38px;height:38px;border-radius:50%;background:#a7a7a7}
.copyright{left:100px;top:126px;font-size:10px;color:#888}
</style>
</head>
<body>

<header class="abs site-header">
  <div class="abs logo">
    <span class="logo-mark"></span>
    <div><div class="logo-name">Kestral Tours</div><div class="logo-tag">The Professional's choice since 1978</div></div>
  </div>
  <div class="abs social"><span></span><span></span><span></span><span></span><span></span></div>
  <div class="abs account-links"><span>SIGN IN</span><span>SIGN UP</span><span>MY ACCOUNT</span></div>
</header>

<nav class="abs main-nav">
  <span class="active">Home</span><span>Travel Agencies</span><span>Religious &amp; Travel Group</span><span>Corporate Concierge</span><span>More Agencies</span><span>Destinations</span><span>About Kestral</span><span>Restricted Area</span>
</nav>

<section class="abs hero">
  <div class="abs hero-plane" role="img" aria-label="Passenger jet climbing through a blue sky with clouds"></div>
  <div class="abs slide-arrow" style="left:0"><svg width="16" height="24"><path d="M13 2 3 12l10 10" stroke="#fff" stroke-width="3" fill="none"/></svg></div>
  <div class="abs slide-arrow" style="right:0"><svg width="16" height="24"><path d="m3 2 10 10L3 22" stroke="#fff" stroke-width="3" fill="none"/></svg></div>

  <div class="abs promo">
    <h1>MORE THAN JUST AIRLINE CONSOLIDATION</h1>
    <div class="stars">★★★★☆</div>
    <div class="reviews">Checkout Our Reviews</div>
  </div>

  <form class="abs signup">
    <div class="field">Enter Your Name</div>
    <div class="field">Enter Your E-mail address</div>
    <div class="cta">Get Access Today!</div>
  </form>

  <form class="abs flight-search">
    <div class="fs-title">FLIGHT SEARCH</div>
    <div class="fs-body">
      <div class="inp dark" style="left:8px;top:12px;width:252px">From: To: (City or airport)</div>
      <div class="inp" style="left:8px;top:52px;width:252px">To: (City or airport)</div>
      <div class="inp" style="left:272px;top:12px;width:240px">Depart Date</div>
      <div class="inp" style="left:272px;top:52px;width:240px">Return Date</div>
      <div class="inp" style="left:524px;top:12px;width:160px">Time</div>
      <div class="inp" style="left:524px;top:52px;width:160px">Time</div>
      <div class="radio" style="left:708px;top:20px"><i class="on"></i>Economy</div>
      <div class="radio" style="left:800px;top:20px"><i></i>First/Business</div>
      <div class="radio" style="left:920px;top:20px"><i></i>Price</div>
      <div class="radio" style="left:708px;top:58px"><i class="on"></i>Schedule</div>
      <div class="radio" style="left:800px;top:58px"><i></i>Reward Travel</div>
      <div class="inp" style="left:8px;top:96px;width:160px">Adults: 12+</div>
      <div class="inp" style="left:8px;top:136px;width:160px">Children: 0-12</div>
      <div class="radio" style="left:180px;top:104px"><i class="on"></i>Round trip</div>
      <div class="radio" style="left:180px;top:142px"><i></i>One Way</div>
      <div class="radio" style="left:272px;top:142px"><i></i>Multiple Destinations</div>
      <div class="fs-link" style="left:524px;top:108px">Find Lower Fare +0 Days</div>
      <div class="fs-link" style="left:524px;top:140px">Search Nearby Airports</div>
      <div class="inp" style="left:708px;top:100px;width:252px">Offer Code (optional)</div>
      <div class="search-btn" style="top:144px">SEARCH</div>
      <div class="fs-link" style="left:850px;top:190px;font-size:12px">Advanced Search</div>
    </div>
  </form>
</section>

<section class="abs agents">
  <h2 class="section-title">Airline Consolidator for Travel Agents</h2>
  <div class="abs agent-col" style="left:70px">
    <svg class="agent-icon" viewBox="0 0 66 66"><circle cx="33" cy="33" r="31" fill="none" stroke="#2f7fc1" stroke-width="2" stroke-dasharray="5 4"/><path d="M20 34 33 22l13 12v12H20z" fill="#2f7fc1"/></svg>
    <h3>Home Based Travel Agents</h3><div class="sub">Find your way to financial freedom!</div>
    <ul><li>• don't lose another client to the big guys</li><li>• get more referrals and more customers!</li></ul>
    <div class="more">learn more</div><span class="btn">Join Now</span>
  </div>
  <div class="abs agent-col" style="left:455px">
    <svg class="agent-icon" viewBox="0 0 66 66"><circle cx="33" cy="33" r="31" fill="none" stroke="#2f7fc1" stroke-width="2" stroke-dasharray="5 4"/><path d="M22 26h22v18H22zM28 26v-4h10v4" fill="none" stroke="#2f7fc1" stroke-width="3"/></svg>
    <h3>Small Travel Agencies</h3><div class="sub">Accelerate your growth!</div>
    <ul><li>• don't lose another client to the big guys</li><li>• get more referrals and more customers!</li></ul>
    <div class="more">learn more</div><span class="btn">Join Now</span>
  </div>
  <div class="abs agent-col" style="left:840px">
    <svg class="agent-icon" viewBox="0 0 66 66"><circle cx="33" cy="33" r="31" fill="none" stroke="#2f7fc1" stroke-width="2" stroke-dasharray="5 4"/><path d="M24 46V20h18v26M28 26h4M34 26h4M28 32h4M34 32h4M28 38h4M34 38h4" fill="none" stroke="#2f7fc1" stroke-width="3"/></svg>
    <h3>Corporate Travel Agencies</h3><div class="sub">Earn &amp; retain higher value clients</div>
    <ul><li>• don't lose another client to the big guys</li><li>• get more referrals and more customers!</li></ul>
    <div class="more">learn more</div><span class="btn">Join Now</span>
  </div>
</section>

<section class="abs welcome">
  <h2 class="section-title">Welcome</h2>
  <p>We're here for our clients!. Over 40 years in business. Locations across the USA. 50+ air carriers . Worldwide • Europe &amp; Middle East travel. Excellent customer service, we staff over 200 agents and have locations in 6 major US cities. Always available … buy in bulk &amp; save even more!</p>
  <span class="btn">Read More</span>
</section>

<section class="abs ceo">
  <div class="abs ceo-photo" role="img" aria-label="Portrait of the company president in a grey suit"></div>
  <blockquote class="abs">“Great airfares are only the beginning, exceptional customer service and caring for our clients is what makes us so unique”</blockquote>
  <div class="abs sig">Mr. Dorvane<br>President &amp; CEO<hr></div>
</section>

<section class="abs divisions">
  <div class="abs col-left">
    <h3>Our Divisions</h3>
    <p>Lorem ipsum dolor sit amet, tatu adipiscing elit, sed diam nonummy euismod tincidunt ut</p>
    <ul><li>• The Airport • Airport Authority</li><li>• Air Cargo • Transfer</li></ul>
    <div class="more">Read more</div>
  </div>
  <div class="abs employees">
    <h3>Our Employees</h3>
    <span class="abs emp-arrow" style="left:10px">‹</span>
    <div class="abs emp" style="left:70px"><div class="photo" role="img" aria-label="Employee portrait"></div><b>Ralf Medo</b>Manager<br>Read more</div>
    <div class="abs emp" style="left:240px"><div class="photo" role="img" aria-label="Employee portrait"></div><b>Tessa Lun</b>Secretary<br>Read more</div>
    <div class="abs emp" style="left:410px"><div class="photo" role="img" aria-label="Employee portrait"></div><b>Oren Vasko</b>Marketing Head<br>Read more</div>
    <span class="abs emp-arrow" style="left:570px">›</span>
    <span class="abs" style="left:540px;top:270px;font-size:12px;color:#555">See all</span>
  </div>
</section>

<section class="abs business">
  <h2 class="section-title">Airline Consolidators for Businesses &amp; Corporations</h2>
  <div class="tag">Tired of travel headaches? Make business travel easy!</div>
  <ul class="abs biz-list">
    <li><span>E</span>Excellent customer service, we staff over 200 agents and have locations in 6 major US cities</li>
    <li><span>A</span>Always available … buy in bulk &amp; save even more!</li>
    <li><span>S</span>Save more by going direct to the consolidator!</li>
    <li><span>Y</span>Your best interests are ours!</li>
  </ul>
  <span class="abs btn">Experience the difference of Kestral!</span>
  <div class="abs agent-photo" role="img" aria-label="Smiling customer service agent wearing a headset"></div>
</section>

<section class="abs places">
  <h2 class="section-title" style="margin-top:10px">There are plenty of places that are worth seeing</h2>
  <div class="abs round-arrow" style="left:82px"><svg width="12" height="16"><path d="M9 2 3 8l6 6" stroke="#fff" stroke-width="2.5" fill="none"/></svg></div>
  <div class="abs round-arrow" style="right:82px"><svg width="12" height="16"><path d="m3 2 6 6-6 6" stroke="#fff" stroke-width="2.5" fill="none"/></svg></div>
  <div class="abs place" style="left:136px"><div class="photo" role="img" aria-label="Tropical resort pool by the sea" style="background:linear-gradient(180deg,#4d9fd8,#2fb7b0 60%,#d9c28f)"></div><h4>LOREM IPSUM</h4><p>Lorem ipsum dolor sit amet,<br>consec tetuer adipiscing</p><div class="price">$ 550.00</div><span class="btn">Contact Us Now</span></div>
  <div class="abs place" style="left:382px"><div class="photo" role="img" aria-label="Ancient Roman amphitheatre under a blue sky" style="background:linear-gradient(180deg,#5f9bd6,#b89a72 55%,#8a6e4f)"></div><h4>LOREM IPSUM</h4><p>Lorem ipsum dolor sit amet,<br>consec tetuer adipiscing</p><div class="price">$ 550.00</div><span class="btn">Contact Us Now</span></div>
  <div class="abs place" style="left:628px"><div class="photo" role="img" aria-label="Snow-capped mountain above an alpine lake" style="background:linear-gradient(180deg,#6fa7de,#e8eef4 40%,#3d7a4d 75%,#2d5a78)"></div><h4>LOREM IPSUM</h4><p>Lorem ipsum dolor sit amet,<br>consec tetuer adipiscing</p><div class="price">$ 550.00</div><span class="btn">Contact Us Now</span></div>
  <div class="abs place" style="left:874px"><div class="photo" role="img" aria-label="Limestone islands rising from turquoise water" style="background:linear-gradient(180deg,#9cc6e8,#4f8c57 45%,#1fa3a3)"></div><h4>LOREM IPSUM</h4><p>Lorem ipsum dolor sit amet,<br>consec tetuer adipiscing</p><div class="price">$ 550.00</div><span class="btn">Contact Us Now</span></div>
  <span class="abs see-all">See all</span>
</section>

<section class="abs group">
  <h2 class="section-title" style="margin-top:4px">Group Travel - Missionary Airfares, Hajj &amp; Umra Discounted Airfares</h2>
  <div class="abs photo" role="img" aria-label="Family group smiling together outdoors" style="left:145px;background:linear-gradient(180deg,#dfe6d8,#a8b58c 50%,#6d6250)"></div>
  <div class="abs photo" role="img" aria-label="Missionary volunteer group posing on grass" style="left:628px;background:linear-gradient(180deg,#8ab8d8,#6b9a4d 40%,#4e7a36)"></div>
  <div class="abs group-card" style="left:145px"><h4>Hajj Group Travel Rates</h4><p>Lorem ipsum dolor sit amet, consectetur adipiscing elit. Nulla quam velit,<br>vulputate eu pharetra nec, mattis ac neque.</p><span class="btn">Contact Us Now</span></div>
  <div class="abs group-card" style="left:628px"><h4>Missionary Travel</h4><p>Lorem ipsum dolor sit amet, consectetur adipiscing elit. Nulla quam velit,<br>vulputate eu pharetra nec, mattis ac neque.</p><span class="btn">Contact Us Now</span></div>
</section>

<section class="abs trusted">
  <h2 class="section-title">Trusted Members of</h2>
  <div class="abs badge" style="left:406px"></div>
  <div class="abs badge" style="left:556px"></div>
  <div class="abs badge" style="left:706px"></div>
</section>

<footer class="abs site-footer">
  <div class="abs footer-logo">
    <span class="logo-mark"></span>
    <div><div class="logo-name" style="color:#666">Kestral Tours</div><div class="logo-tag">The Professional's choice since 1978</div></div>
  </div>
  <div class="abs contact">
    <div><svg width="10" height="12"><path d="M5 1a4 4 0 0 1 4 4c0 3-4 7-4 7S1 8 1 5a4 4 0 0 1 4-4z" fill="#999"/></svg>742 Linden Street Suite 300, Brookvale NY</div>
    <div><svg width="10" height="12"><path d="M2 1h3l1 3-2 1a6 6 0 0 0 3 3l1-2 3 1v3c-6 0-9-3-9-9z" fill="#999"/></svg>+1 555 0142 780</div>
    <div><svg width="10" height="12"><rect x="0" y="2" width="10" height="8" fill="#999"/></svg>hello@kestraltours.example</div>
  </div>
  <div class="abs footer-social"><span></span><span></span><span></span><span></span><span></span></div>
  <div class="abs copyright">© 2014 PRIVACY POLICY</div>
</footer>

</body>
</html>
```